Modern Business Card For A Digital Advertising Company

I'll be print on the Pell Prints Velour paper http://us.pellprints.com/products/velour/business-cards.html
Need's to be modern and use the color palette of the logo or gray scales. I think integrating the pixelation of the logo in to the card and having it wrap from one side to the other could be interesting. My company provides ad operations, web development, and number of other services to websites around the world. You can see my website at http://www.zantorhq.com
Contact info on the card needs to have
Owen Lasko
President
p.318.204.6637
owen@zantorhq.com
http://www.zantorhq.com
Doesn't necessarily need to be in that order
Website owners
Business

```html
<!DOCTYPE html>
<html lang="en">
<head>
<meta charset="utf-8">
<title>Zantor Business Card</title>
<link rel="stylesheet" href="https://fonts.googleapis.com/css2?family=Mulish:wght@400;600;800&display=swap">
<style>
  :root {
    --backdrop: #d9d9db;
    --card-white: #ffffff;
    --green-light: #8cc63f;
    --green-mid: #76ad3c;
    --green-dark: #5b8a38;
    --ink-gray: #555a5e;
    --swoosh-dark: #2f3133;
    --swoosh-gray: #9a9d9f;
  }
  * { margin: 0; padding: 0; box-sizing: border-box; }
  html, body { width: 1200px; height: 450px; overflow: hidden; }
  body {
    background: var(--backdrop);
    font-family: "Mulish", "Century Gothic", sans-serif;
    position: relative;
  }
  .card {
    position: absolute;
    top: 78px;
    width: 524px;
    height: 300px;
    border-radius: 24px;
    overflow: hidden;
    box-shadow: 0 2px 6px rgba(0,0,0,0.18);
  }
  .card-front { left: 58px; background: var(--card-white); }
  .card-back {
    left: 622px;
    background: linear-gradient(90deg, var(--green-light) 0%, var(--green-mid) 50%, var(--green-dark) 100%);
  }
  .front-wave { position: absolute; left: 0; top: 0; }
  .contact-list {
    position: absolute;
    left: 54px;
    top: 52px;
    list-style: none;
  }
  .contact-item {
    display: flex;
    align-items: center;
    gap: 6px;
    height: 22.5px;
    font-size: 15px;
    color: var(--ink-gray);
  }
  .contact-icon { width: 10px; height: 10px; flex: none; }
  .brand-front {
    position: absolute;
    left: 286px;
    top: 150px;
    width: 220px;
    display: flex;
    align-items: center;
    gap: 10px;
  }
  .brand-square { width: 26px; height: 26px; background: var(--green-light); flex: none; }
  .brand-name-front {
    font-size: 46px;
    font-weight: 800;
    color: var(--green-light);
    letter-spacing: 1px;
    line-height: 1;
  }
  .holder {
    position: absolute;
    left: 54px;
    top: 242px;
    color: var(--card-white);
  }
  .holder-name { font-size: 19px; font-weight: 800; line-height: 1.1; }
  .holder-title { font-size: 14px; font-weight: 400; line-height: 1.4; }
  .brand-back {
    position: absolute;
    left: 0;
    right: 0;
    top: 92px;
    display: flex;
    justify-content: center;
    align-items: center;
    gap: 16px;
  }
  .brand-back .brand-square { width: 40px; height: 40px; background: var(--card-white); }
  .brand-name-back {
    font-size: 72px;
    font-weight: 800;
    color: var(--card-white);
    letter-spacing: 2px;
    line-height: 1;
  }
  .back-url {
    position: absolute;
    left: 0;
    right: 0;
    top: 240px;
    text-align: center;
    font-size: 21px;
    letter-spacing: 1.5px;
    color: var(--card-white);
  }
</style>
</head>
<body>
  <section class="card card-front">
    <svg class="front-wave" width="524" height="300" viewBox="0 0 524 300" aria-hidden="true">
      <defs>
        <linearGradient id="waveGreen" x1="0" x2="1" y1="0" y2="0">
          <stop offset="0" stop-color="#8cc63f"/>
          <stop offset="1" stop-color="#5b8a38"/>
        </linearGradient>
      </defs>
      <path d="M0,222 C110,196 230,205 320,240 C400,270 470,262 524,240 L524,228 C470,250 400,258 320,230 C230,194 110,186 0,208 Z" fill="var(--swoosh-gray)"/>
      <path d="M0,226 C110,200 230,210 320,246 C360,262 390,266 420,266 C380,262 350,254 320,240 C230,200 110,192 0,214 Z" fill="var(--swoosh-dark)"/>
      <path d="M0,232 C110,208 230,218 320,254 C400,284 470,272 524,252 L524,300 L0,300 Z" fill="url(#waveGreen)"/>
    </svg>

    <ul class="contact-list">
      <li class="contact-item">
        <svg class="contact-icon" viewBox="0 0 10 10" aria-hidden="true"><circle cx="5" cy="5" r="5" fill="var(--green-light)"/><path d="M3,2.5 L4.3,2.5 L4.6,4 L3.9,4.5 C4.3,5.3 4.7,5.7 5.5,6.1 L6,5.4 L7.5,5.7 L7.5,7 C5,7.2 2.8,5 3,2.5 Z" fill="#fff"/></svg>
        <span>318.204.6637</span>
      </li>
      <li class="contact-item">
        <svg class="contact-icon" viewBox="0 0 10 10" aria-hidden="true"><circle cx="5" cy="5" r="5" fill="var(--green-light)"/><rect x="2.4" y="3.2" width="5.2" height="3.6" fill="#fff"/><path d="M2.4,3.2 L5,5.2 L7.6,3.2" fill="none" stroke="var(--green-light)" stroke-width="0.6"/></svg>
        <span>owen@zantorhq.com</span>
      </li>
      <li class="contact-item">
        <svg class="contact-icon" viewBox="0 0 10 10" aria-hidden="true"><circle cx="5" cy="5" r="5" fill="var(--green-light)"/><path d="M1.5,5 H8.5 M5,1.5 C3.4,3.5 3.4,6.5 5,8.5 M5,1.5 C6.6,3.5 6.6,6.5 5,8.5" fill="none" stroke="#fff" stroke-width="0.7"/></svg>
        <span>www.zantorhq.com</span>
      </li>
    </ul>

    <div class="brand-front">
      <span class="brand-square" aria-hidden="true"></span>
      <span class="brand-name-front">Zantor</span>
    </div>

    <div class="holder">
      <p class="holder-name">Owen Lasko</p>
      <p class="holder-title">President</p>
    </div>
  </section>

  <section class="card card-back">
    <div class="brand-back">
      <span class="brand-square" aria-hidden="true"></span>
      <span class="brand-name-back">Zantor</span>
    </div>
    <p class="back-url">www.zantorhq.com</p>
  </section>
</body>
</html>
```